Lantern Petals Website v.1 - attract floral shop franchisees

I need a simple information website for my new business. We are a franchisor of flower shops. The overall purpose of the website is to promote the company and the service, especially to potential franchisees and retailers. Only about 4 pages are required including homepage, About, For Supermarkets, For Franchisees, and Contact. No special functions are required except the site will have two separate inquiry forms that must be filled out online and submitted via automated email. Similarly, an email form should be linked from the Contact page. I have a logo and business cards designed by ArtMingle, and I would like the site to have a consistent color scheme and style. The key to design will be to express the joy and love associated with flowers and floral bouquets.
IMPORTANT - I will be exporting the website design to Wordpress CMS in a site hosted by HostNimbus. For smooth integration into WordPress hosted by HostNimbus, the designer should build the site using a WordPress-friendly format. Ideally, they should use HTML, CSS, and PHP. Creating a custom theme or using a page builder that exports to WordPress-compatible files is best. This ensures the site can be easily imported and managed within WordPress.

Target Market(s)

Potential franchisees (existing florists or creative types who might like to own a floral business) and supermarkets who might want us to run their floral department

Industry/Entity Type

Floral retailing

Requirements
Must have
• A brand theme that is beautiful, consistent throughout and builds on the logo design
Nice to have
• Show gender and ethnic diversity in customers and florists. Pictures of happy florists (for franchisees) and pictures of amazing floral department displays (for supermarkets)

```html
<!DOCTYPE html>
<html lang="en">
<head>
<meta charset="utf-8">
<title>Lantern Petals</title>
<link href="https://fonts.googleapis.com/css2?family=Abhaya+Libre:wght@700;800&family=Poppins:wght@400;500&display=swap" rel="stylesheet">
<style>
:root{
  --green:#0a8c45;
  --green-deep:#0e7a3d;
  --orange:#f2a327;
  --ink:#1d1d1d;
  --grey-bg:#f7f7f7;
  --white:#ffffff;
}
*{box-sizing:border-box;margin:0;padding:0}
html,body{width:1200px;height:3577px;overflow:hidden;background:var(--white)}
body{position:relative;font-family:"Poppins",sans-serif;color:var(--ink)}
.abs{position:absolute}
.serif{font-family:"Abhaya Libre",serif;font-weight:800}
.brand-name{font-family:"Poppins",sans-serif;font-weight:500;color:var(--green);display:flex;align-items:center;gap:8px}
.brand-dot{width:14px;height:14px;border-radius:50%;background:var(--orange)}
.btn{position:absolute;background:var(--orange);color:var(--white);font-size:12px;font-weight:500;display:flex;align-items:center;justify-content:center;border-radius:4px 12px 4px 4px}
.label{color:var(--orange);font-size:11px;text-transform:uppercase}
.heading{font-size:32px;line-height:36px;color:var(--ink)}
.body-text{font-size:12.5px;line-height:22px}
.photo{position:absolute}
.circle{position:absolute;border-radius:50%}
/* header */
.site-header{top:0;left:0;width:1200px;height:92px;background:var(--white)}
.menu-icon{left:1051px;top:35px;width:34px}
.menu-icon span{display:block;height:3px;background:var(--ink);margin-bottom:7px}
/* hero */
.hero{top:92px;left:0;width:1200px;height:431px;background:linear-gradient(90deg,#c98a8f 0%,#d8cfc4 25%,#e4cfae 50%,#d9cdc1 75%,#c7b7a8 100%)}
.hero-title{top:288px;left:0;width:1200px;text-align:center;font-size:44px;line-height:46px}
.hero-sub{top:388px;left:0;width:1200px;text-align:center;font-family:"Abhaya Libre",serif;font-weight:700;font-size:14px}
/* sections */
.supermarket{top:1170px;left:0;width:1200px;height:572px;background:var(--grey-bg)}
.footer{top:3332px;left:0;width:1200px;height:245px;background:var(--green-deep)}
.gallery-cell{position:absolute;width:242px}
</style>
</head>
<body>

<header class="abs site-header">
  <div class="abs brand-name" style="left:107px;top:32px;font-size:20px"><span class="brand-dot"></span>Lantern Petals</div>
  <div class="abs menu-icon"><span></span><span></span><span></span></div>
</header>

<section class="abs hero" role="img" aria-label="Florist hands arranging tulips and roses on a wooden table with ribbon and scissors"></section>
<div class="abs brand-name" style="left:0;width:1200px;justify-content:center;top:270px;font-size:12px;font-weight:500"><span class="brand-dot" style="width:10px;height:10px"></span>LANTERN PETALS</div>
<h1 class="abs serif hero-title">Fresh Flowers Convey<br>Special Sentiments</h1>
<p class="abs hero-sub">love, happiness, joy - which every person deserves.</p>
<a class="btn" style="left:568px;top:428px;width:137px;height:43px">Get Started</a>

<!-- About -->
<div class="photo" style="left:0;top:620px;width:155px;height:460px;background:linear-gradient(180deg,#f5a623,#e86c1a);border-radius:0 80px 80px 0" role="img" aria-label="Orange gerbera daisies"></div>
<h2 class="abs serif heading" style="left:190px;top:682px">About Lantern Petals</h2>
<p class="abs body-text" style="left:190px;top:731px;width:390px;font-size:12.5px;line-height:19.5px">Fresh flowers convey special sentiments - love, happiness, joy which every person deserves. Lantern Petals is an entrepreneurial company created to make top quality fresh flowers and artisan-designed bouquets accessible to every consumer at affordable prices.<br><br>Lantern Petals brings the best of professional florists and supermarkets together for the benefit of consumers. It supports a national network of</p>
<a class="btn" style="left:192px;top:927px;width:105px;height:29px">Read More</a>
<div class="photo" style="left:985px;top:612px;width:160px;height:155px;background:var(--orange);border-radius:30px" role="img" aria-label="Orange honeycomb accent"></div>
<div class="circle" style="left:656px;top:616px;width:414px;height:414px;border:15px solid var(--green);background:linear-gradient(135deg,#8d8a45,#c9a98a)" role="img" aria-label="Two smiling women holding a colourful bouquet"></div>

<!-- Supermarkets -->
<section class="abs supermarket"></section>
<div class="photo" style="left:56px;top:1247px;width:150px;height:175px;background:var(--orange);border-radius:30px" role="img" aria-label="Orange honeycomb accent"></div>
<div class="circle" style="left:128px;top:1253px;width:414px;height:414px;border:15px solid var(--orange);background:linear-gradient(135deg,#d9677a,#2a7f86)" role="img" aria-label="Smiling florist in a teal shirt tending pink flowers"></div>
<p class="abs label" style="left:584px;top:1303px">For Supermarkets</p>
<h2 class="abs serif heading" style="left:584px;top:1318px;width:520px">Supermarket Flower Departments Benefit</h2>
<p class="abs body-text" style="left:580px;top:1398px;width:460px">However their quality of stems and bouquets is often poor and in-store service is limited. In contrast, professional florists typically sell the finest quality stems, design the most beautiful bouquets and provide the finest customer service, but their costs and customer prices are high. Supermarkets find that Lantern Petals, through their florist franchise network, is able to improve their financial outcomes, provide attentive customer service and satisfaction, and lift the quality of the entire store environment</p>
<a class="btn" style="left:579px;top:1588px;width:172px;height:30px">More For Supermarket</a>

<!-- Franchisees -->
<div class="photo" style="left:970px;top:1765px;width:100px;height:225px;background:linear-gradient(180deg,#0a8c45,#f2a327);border-radius:50px;opacity:.85" role="img" aria-label="Bee illustration with dotted flight path"></div>
<p class="abs label" style="left:0;width:565px;text-align:right;top:1867px">For Franchisees</p>
<h2 class="abs serif heading" style="left:0;width:567px;text-align:right;top:1883px">National Network Of Owner<br>Operator Franchisees</h2>
<p class="abs body-text" style="left:105px;width:460px;text-align:right;top:1963px">Our franchisees are the cornerstone of our business. Many of them are already professional florists or florist employees who wish to expand their businesses without the significant costs of a traditional flower shop. Others are creative types or flower lovers who have made a career change in order to express their talents and make people happy. Still others are entrepreneurs in search of owning their own business. All are welcome if they meet Lantern Petals' high standards of quality, service and ethical business practices</p>
<a class="btn" style="left:390px;top:2155px;width:175px;height:31px">More For Franchisees</a>
<div class="circle" style="left:633px;top:1838px;width:414px;height:414px;border:15px solid var(--green);background:linear-gradient(135deg,#c9c3b5,#d5c93a)" role="img" aria-label="Smiling florist holding a wrapped bouquet"></div>
<div class="photo" style="left:0;top:2148px;width:140px;height:262px;background:var(--orange);border-radius:0 40px 40px 0" role="img" aria-label="Orange honeycomb accent"></div>

<!-- Gallery -->
<h2 class="abs serif" style="left:0;width:1200px;text-align:center;top:2318px;font-size:32px">Our Gallery</h2>
<p class="abs" style="left:0;width:1200px;text-align:center;top:2375px;font-size:12.5px">Inspirational photos highlighting store layouts, product displays, and customer experiences.</p>
<div class="gallery-cell" style="left:209px;top:2425px;height:169px;background:linear-gradient(135deg,#9aa3a8,#a8202a)" role="img" aria-label="Hands holding a red bouquet"></div>
<div class="gallery-cell" style="left:209px;top:2605px;height:363px;background:linear-gradient(135deg,#2f5a3a,#f0b23a)" role="img" aria-label="Hands wrapping a yellow and orange bouquet"></div>
<div class="gallery-cell" style="left:460px;top:2425px;height:363px;background:linear-gradient(135deg,#e9e9e6,#d24a3a)" role="img" aria-label="Woman holding white flowers"></div>
<div class="gallery-cell" style="left:460px;top:2798px;height:170px;background:linear-gradient(135deg,#f4a6bf,#f7e9ee)" role="img" aria-label="Couple with a bouquet on a pink backdrop"></div>
<div class="gallery-cell" style="left:711px;top:2425px;height:169px;background:linear-gradient(135deg,#c09580,#e8d13a)" role="img" aria-label="Woman arranging flowers"></div>
<div class="gallery-cell" style="left:711px;top:2605px;height:363px;background:linear-gradient(135deg,#6c7c8f,#d9607a)" role="img" aria-label="Bouquet handed across a counter"></div>
<div class="photo" style="left:1020px;top:2545px;width:180px;height:320px;background:var(--green);border-radius:100px 0 0 100px;opacity:.9" role="img" aria-label="Green leaf branch"></div>
<a class="btn" style="left:548px;top:3006px;width:104px;height:34px">View Gallery</a>

<!-- Contact band -->
<div class="abs" style="left:107px;top:3154px;width:977px;height:192px;background:var(--orange)"></div>
<div class="photo" style="left:165px;top:3040px;width:350px;height:306px;background:linear-gradient(180deg,#d86ab0,#8cc63f);border-radius:150px 150px 20px 20px" role="img" aria-label="Vase of pink lilies and mixed flowers"></div>
<p class="abs serif" style="left:540px;top:3226px;font-size:25px;line-height:27px;color:var(--white);font-weight:700">For questions and further information,<br>contact <u>info@Lantern-Petals.com</u></p>

<!-- Footer -->
<footer class="abs footer">
  <div class="abs brand-name" style="left:0;width:1200px;justify-content:center;top:72px;font-size:26px;color:var(--white)"><span class="brand-dot"></span>Lantern Petals</div>
  <div class="abs" style="left:531px;top:144px;display:flex;gap:11px">
    <span style="width:27px;height:27px;border-radius:50%;background:rgba(255,255,255,.3)"></span>
    <span style="width:27px;height:27px;border-radius:50%;background:rgba(255,255,255,.3)"></span>
    <span style="width:27px;height:27px;border-radius:50%;background:rgba(255,255,255,.3)"></span>
    <span style="width:27px;height:27px;border-radius:50%;background:rgba(255,255,255,.3)"></span>
  </div>
  <div class="abs" style="left:183px;top:203px;width:850px;height:1px;background:rgba(255,255,255,.25)"></div>
  <p class="abs" style="left:185px;top:218px;font-size:10px;color:var(--white)">© 2024 Lantern Petals, All rights reserved</p>
  <p class="abs" style="left:820px;top:218px;font-size:10px;color:var(--white)">Terms &amp; conditions</p>
  <p class="abs" style="left:957px;top:218px;font-size:10px;color:var(--white)">Privacy policy</p>
</footer>

</body>
</html>
```